Vorelan.com Personal Trainer/Fitness Website

I want a website to market my personal training/Outdoor Bootcamp Class services, as well as to ditribute nutrivex. I need a logo as well I included an address for the Harbor Gales 1975 logo. I'd like Vorelan in place of Harbor Gales, and in Black and white, just different enough so I can't get sued by the PBL.
https://www.pictofind.example/imgres?imgurl=http%3A%2F%2Fwww.darnell-quibury.example%2Fwp-content%2Fuploads%2F2014%2F01%2Fgales_logo4.jpg&imgrefurl=http%3A%2F%2Fwww.darnell-quibury.example%2Fpbl-logo-redesigns-harbor-gales%2F&docid=_qkwzR7TBAgXpL&tbnid=m4tpU8KdOXjnRP%3A&w=600&h=450&client=ms-android-carrier&bih=512&biw=360&ved=0ahUKEwiRtpgyp9HMAhUTwGMKHRPMBWMQMwg6KBQwFA&iact=mrc&uact=8.
It should be about 5 pages 1. home 2. about 3. Services 4. Blog/Videos and programs 5. Contact.
http://www.dorvinfitness.example.uk/ is a website I like the style of.

Target Market(s)

Seattle area

Industry/Entity Type

Fitness

Coding

Coded - Design and coding required

Number of Pages Required

4 page

Font styles to use
Serif
Sans Serif

Requirements
Must have
• A minimal look
Nice to have
• A logo similar to the 1975 Harbor Galewinds Logo, with a Small Milo Brandt ripping his shirt open(with a picture of the logo on his shirt, picture within picture) to turn into Ironjaw in the center. Skyline is black, Background and small figure white(with black logo on shirt)

```html
<!DOCTYPE html>
<html lang="en">
<head>
<meta charset="utf-8">
<title>Vorelan – Personal &amp; Group Training</title>
<link rel="stylesheet" href="https://fonts.googleapis.com/css2?family=Roboto:wght@400;500;700&family=Lato:ital,wght@0,400;0,700;1,400&family=Exo+2:wght@700;800&display=swap">
<style>
:root{
  --green:#0a6b35;
  --green-dark:#07562a;
  --red:#e8141b;
  --black:#000;
  --footer:#262626;
  --footer-line:#444;
  --white:#fff;
  --grey-text:#333;
  --sans:'Roboto',Arial,sans-serif;
  --body:'Lato',Arial,sans-serif;
  --display:'Exo 2',Arial,sans-serif;
}
*{box-sizing:border-box;margin:0;padding:0}
html,body{width:1200px;height:2446px;overflow:hidden;background:#fff}
body{position:relative;font-family:var(--body);color:var(--grey-text)}
.abs{position:absolute}

/* header */
.site-header{position:absolute;top:0;left:0;width:1200px;height:134px;background:#fff;border-top:3px solid #111}
.brand{position:absolute;left:80px;top:40px;display:flex;align-items:center;gap:10px}
.brand-mark{width:38px;height:38px;border-radius:50%;background:var(--green)}
.brand-name{font-family:var(--sans);font-weight:700;font-size:34px;color:var(--green);letter-spacing:1px}
.join-btn{position:absolute;left:905px;top:22px;width:215px;height:45px;background:var(--red);color:#fff;border-radius:5px;font-family:var(--sans);font-size:23px;display:flex;align-items:center;justify-content:center;letter-spacing:.5px}
.header-contact{position:absolute;left:853px;top:84px;display:flex;align-items:center;gap:10px}
.phone-icon{width:32px;height:32px;border-radius:50%;background:var(--green);display:flex;align-items:center;justify-content:center}
.header-phone{font-family:var(--sans);font-weight:700;font-size:22px;color:#111;margin-right:12px}
.social-dot{width:30px;height:30px;border-radius:50%}
.social-dot.blue{background:#1d5fa8}
.social-dot.brown{background:#8a6a4f}

/* nav */
.main-nav{position:absolute;top:134px;left:0;width:1200px;height:45px;background:var(--green);border-top:2px solid #0c7b3e}
.main-nav ul{list-style:none;display:flex;position:absolute;left:80px;top:0;height:43px}
.main-nav li{height:43px;display:flex;align-items:center;justify-content:center;font-family:var(--sans);font-weight:500;font-size:14px;color:#fff;letter-spacing:1px;border-right:1px solid rgba(255,255,255,.25)}
.main-nav li.active{background:#050505}

/* hero */
.hero{position:absolute;top:179px;left:0;width:1200px;height:621px;background:linear-gradient(180deg,#8fb9d9 0%,#c9dde8 20%,#3d6b2b 30%,#4f7f31 45%,#6e9a3e 70%,#5f8d36 100%)}
.hero-panel{position:absolute;left:713px;top:184px;width:407px;height:257px;background:rgba(40,40,40,.82);display:flex;flex-direction:column;justify-content:center;align-items:flex-end;padding-right:30px;color:#fff;font-family:var(--display);font-weight:800;text-align:right;line-height:1.25}
.hero-panel .l1{font-size:33px}
.hero-panel .l2{font-size:33px}
.hero-panel .l2 b{font-size:40px}
.hero-panel .l3{font-size:40px}

/* about */
.about{position:absolute;top:800px;left:0;width:1200px;height:281px;background:var(--black);color:#fff;text-align:center}
.about h2{font-family:var(--sans);font-weight:700;font-size:26px;margin-top:40px}
.about p{font-size:14.5px;line-height:24px;width:1090px;margin:16px auto 0}
.pill-btn{display:inline-block;margin-top:24px;background:var(--green);color:#fff;font-family:var(--sans);font-weight:700;font-size:12px;letter-spacing:1px;padding:7px 16px;border-radius:16px}

/* services */
.services{position:absolute;top:1081px;left:0;width:1200px;height:437px;background:linear-gradient(90deg,#6a6a6a,#7d7a78 40%,#5f5f60 70%,#767371)}
.section-title{font-family:var(--sans);font-weight:700;font-size:27px;text-align:center}
.rule{width:80px;height:3px;background:var(--red);margin:0 auto}
.services .section-title{color:#fff;margin-top:60px}
.services .rule{margin-top:12px}
.services .sub{color:#fff;font-family:var(--sans);font-size:18px;text-align:center;margin-top:26px}
.service{position:absolute;top:208px;width:260px;margin-left:-130px;text-align:center}
.service-icon{width:118px;height:118px;border-radius:50%;background:var(--green);border:5px solid #d8d8d8;margin:0 auto}
.service-label{color:#fff;font-family:var(--sans);font-weight:700;font-size:15px;margin-top:28px}

/* reviews */
.reviews{position:absolute;top:1518px;left:0;width:1200px;height:421px;background:#fff}
.reviews .section-title{color:var(--green);margin-top:46px}
.reviews .rule{margin-top:16px}
.review-box{position:absolute;left:80px;top:129px;width:1040px;height:177px;border:1px solid #ddd;border-radius:8px;padding:18px 30px;font-style:italic;font-size:15px;line-height:25px;text-align:center;color:#222}
.review-tail{position:absolute;left:510px;top:305px}
.stars{position:absolute;left:355px;top:333px;display:flex;gap:6px}
.reviewer{position:absolute;left:355px;top:360px;font-family:var(--sans);font-size:15px;color:var(--green)}
.reviewer b{font-weight:700}

/* footer */
.site-footer{position:absolute;top:1939px;left:0;width:1200px;height:458px;background:var(--footer);color:#fff}
.newsletter{position:absolute;left:80px;top:52px;width:758px;height:71px;border:1px solid var(--green);border-radius:3px;display:flex;align-items:center;padding-left:14px}
.newsletter h3{font-family:var(--sans);font-weight:700;font-size:19px;margin-left:10px;width:222px}
.newsletter .email-field{width:384px;height:36px;background:#fff;color:#333;font-size:13px;display:flex;align-items:center;padding-left:10px}
.newsletter .subscribe{width:98px;height:36px;background:var(--green);font-family:var(--sans);font-weight:700;font-size:13px;display:flex;align-items:center;justify-content:center}
.follow{position:absolute;left:888px;top:72px;display:flex;align-items:center;gap:14px;font-family:var(--sans);font-weight:700;font-size:19px}
.col-title{position:absolute;display:flex;align-items:center;gap:10px;font-family:var(--sans);font-weight:700;font-size:19px}
.col-title .ico{width:26px;height:26px;border-radius:50%;border:2px solid #999}
.col-rule{position:absolute;height:2px;background:#555}
.field{position:absolute;border:1px solid #bbb;border-radius:3px;font-size:13px;padding:10px 12px;color:#eee}
.submit{position:absolute;background:var(--green);font-family:var(--sans);font-weight:700;font-size:14px;display:flex;align-items:center;justify-content:center;border-radius:3px}
.vline{position:absolute;width:1px;background:var(--footer-line)}
.quick-links{position:absolute;left:627px;top:2168px;list-style:none;font-family:var(--sans);font-size:13px}
.quick-links li{height:29.3px;display:flex;align-items:center;gap:10px}
.contact-line{position:absolute;left:865px;display:flex;align-items:center;gap:12px}
.contact-line .ico{width:32px;height:32px;border-radius:50%;border:2px solid #fff;background:var(--green);display:flex;align-items:center;justify-content:center}
.footer-brand{position:absolute;left:865px;top:2285px;display:flex;align-items:center;gap:8px}
.footer-brand .brand-name{font-size:30px}
.copyright{position:absolute;top:2397px;left:0;width:1200px;height:49px;background:#111;border-top:2px solid var(--red);color:#fff;font-size:12px;display:flex;align-items:center;justify-content:center}
.up-tab{position:absolute;left:590px;top:2384px}
</style>
</head>
<body>

<header class="site-header">
  <div class="brand"><span class="brand-mark"></span><span class="brand-name">VORELAN</span></div>
  <div class="join-btn">JOIN A SESSION</div>
  <div class="header-contact">
    <span class="phone-icon"><svg width="16" height="16" viewBox="0 0 24 24"><path fill="#fff" d="M6.6 10.8a15 15 0 0 0 6.6 6.6l2.2-2.2c.3-.3.7-.4 1-.2 1.1.4 2.3.6 3.6.6.6 0 1 .4 1 1V20c0 .6-.4 1-1 1C10.6 21 3 13.4 3 4c0-.6.4-1 1-1h3.5c.6 0 1 .4 1 1 0 1.2.2 2.4.6 3.6.1.3 0 .7-.2 1z"/></svg></span>
    <span class="header-phone">123-345-5678</span>
    <span class="social-dot blue"></span>
    <span class="social-dot brown"></span>
  </div>
</header>

<nav class="main-nav">
  <ul>
    <li class="active" style="width:134px">HOME</li>
    <li style="width:138px">ABOUT</li>
    <li style="width:157px">SERVICES</li>
    <li style="width:130px">BLOG</li>
    <li style="width:144px">VIDEOS</li>
    <li style="width:172px">PROGRAMS</li>
    <li style="width:163px">CONTACT</li>
  </ul>
</nav>

<section class="hero" role="img" aria-label="Trainer coaching a client using battle ropes on a grassy park field">
  <div class="hero-panel">
    <div class="l1">WHERE PERSONAL</div>
    <div class="l2">TRAINING <b>MEETS</b></div>
    <div class="l3">GROUP TRAINING</div>
  </div>
</section>

<section class="about">
  <h2>ABOUT VORELAN</h2>
  <p>Lorem ipsum dolor sit amet, consectetuer adipiscing elit, sed diam nonummy nibh euismod tincidunt ut laoreet dolore magna aliquam erat sit volutpat. Ut wisi enim ad minim veniam, quis nostrud exerci tation ullamcorper suscipit lobortis nisl ut aliquip ex ea commodo consequat. Duis autem vel eum iriure dolor in hendrerit in vulputate velit esse molestie consequat, vel illum dolore eu feugiat nulla facilisis at vero eros et sit accumsan et iusto odio dignissim qui blandit praesent luptatum zzril delenit augue duis dolore te feugait nulla facilisi.</p>
  <span class="pill-btn">READ MORE</span>
</section>

<section class="services" role="img" aria-label="Group stretching class in a bright studio, shown under a grey overlay">
  <h2 class="section-title">OUR SERVICES</h2>
  <div class="rule"></div>
  <div class="sub">SELECT TO LEARN MORE!</div>
  <div class="service" style="left:183px"><div class="service-icon" role="img" aria-label="Personal training pictogram"></div><div class="service-label">PERSONAL TRAINING</div></div>
  <div class="service" style="left:447px"><div class="service-icon" role="img" aria-label="Bootcamp class pictogram"></div><div class="service-label">OUTDOOR BOOTCAMP CLASSES</div></div>
  <div class="service" style="left:729px"><div class="service-icon" role="img" aria-label="Group running pictogram"></div><div class="service-label">OUTDOOR GROUP TRAINING</div></div>
  <div class="service" style="left:1008px"><div class="service-icon" role="img" aria-label="Online coaching pictogram"></div><div class="service-label">ONLINE COACHING</div></div>
</section>

<section class="reviews">
  <h2 class="section-title">CLIENT REVIEWS</h2>
  <div class="rule"></div>
  <div class="review-box">“ I have been training with Darius for just a few weeks now and am already feeling a difference between this and past efforts to get healthy. He's exactly what I was looking for- someone who has been where I am and knows what it's like to have to work hard to lose the weight and learn what it takes to get healthy. From his comprehensive initial assessment (and I mean comprehensive- you will work!) to a customized training plan (not off the shelf- it's what your specific body needs) and great group classes, Darius offers it all. I get both the 1:1 attention and the energy from being with other folks in a class. ”</div>
  <svg class="review-tail" width="40" height="40" viewBox="0 0 40 40"><path d="M0 0 L10 38 L36 0" fill="#fff" stroke="#ddd"/><rect x="1" y="0" width="34" height="2" fill="#fff"/></svg>
  <div class="stars">
    <svg width="18" height="18" viewBox="0 0 24 24"><path fill="#aaa" d="M12 2l3 7 7 .6-5.3 4.7 1.6 7.2L12 17.8 5.7 21.5l1.6-7.2L2 9.6 9 9z"/></svg>
    <svg width="18" height="18" viewBox="0 0 24 24"><path fill="#aaa" d="M12 2l3 7 7 .6-5.3 4.7 1.6 7.2L12 17.8 5.7 21.5l1.6-7.2L2 9.6 9 9z"/></svg>
    <svg width="18" height="18" viewBox="0 0 24 24"><path fill="#aaa" d="M12 2l3 7 7 .6-5.3 4.7 1.6 7.2L12 17.8 5.7 21.5l1.6-7.2L2 9.6 9 9z"/></svg>
    <svg width="18" height="18" viewBox="0 0 24 24"><path fill="#aaa" d="M12 2l3 7 7 .6-5.3 4.7 1.6 7.2L12 17.8 5.7 21.5l1.6-7.2L2 9.6 9 9z"/></svg>
    <svg width="18" height="18" viewBox="0 0 24 24"><path fill="#555" d="M12 2l3 7 7 .6-5.3 4.7 1.6 7.2L12 17.8 5.7 21.5l1.6-7.2L2 9.6 9 9z"/></svg>
  </div>
  <div class="reviewer"><b>Ned P. on</b> March 20, 2016</div>
</section>

<footer class="site-footer">
  <div class="newsletter">
    <svg width="26" height="22" viewBox="0 0 26 22"><rect x="1" y="4" width="24" height="16" rx="2" fill="#777"/><path d="M1 6 L13 14 L25 6" stroke="#333" stroke-width="2" fill="none"/></svg>
    <h3>NEWSLETTER SIGNUP</h3>
    <div class="email-field">Enter your email here</div>
    <div class="subscribe">SUBSCRIBE</div>
  </div>
  <div class="follow">FOLLOW US <span class="social-dot blue"></span><span class="social-dot brown" style="margin-left:-4px"></span></div>
</footer>

<div class="col-title" style="left:80px;top:2099px"><span class="ico"></span>QUICK INQUIRY</div>
<div class="col-rule" style="left:80px;top:2140px;width:164px"></div>
<div class="field" style="left:80px;top:2170px;width:226px;height:40px">Name</div>
<div class="field" style="left:324px;top:2170px;width:230px;height:98px">Message</div>
<div class="field" style="left:80px;top:2228px;width:226px;height:40px">Email Address</div>
<div class="field" style="left:80px;top:2286px;width:226px;height:40px">Phone Number</div>
<div class="submit" style="left:324px;top:2286px;width:226px;height:40px;color:#fff">SUBMIT</div>

<div class="vline" style="left:592px;top:2100px;height:250px"></div>
<div class="vline" style="left:832px;top:2100px;height:250px"></div>

<div class="col-title" style="left:627px;top:2106px;color:#fff"><span class="ico" style="border-radius:3px"></span>QUICK LINKS</div>
<div class="col-rule" style="left:627px;top:2146px;width:160px"></div>
<ul class="quick-links" style="color:#fff">
  <li>›&nbsp;HOME</li><li>›&nbsp;ABOUT</li><li>›&nbsp;SERVICES</li><li>›&nbsp;BLOG</li><li>›&nbsp;VIDEOS</li><li>›&nbsp;PROGRAMS</li><li>›&nbsp;CONTACT</li>
</ul>

<div class="col-title" style="left:865px;top:2106px;color:#fff"><span class="ico"></span>CONTACT DETAILS</div>
<div class="col-rule" style="left:865px;top:2146px;width:170px"></div>
<div class="contact-line" style="top:2166px;color:#fff;font-family:var(--sans);font-weight:500;font-size:19px"><span class="ico"><svg width="14" height="14" viewBox="0 0 24 24"><path fill="#fff" d="M6.6 10.8a15 15 0 0 0 6.6 6.6l2.2-2.2c.3-.3.7-.4 1-.2 1.1.4 2.3.6 3.6.6.6 0 1 .4 1 1V20c0 .6-.4 1-1 1C10.6 21 3 13.4 3 4c0-.6.4-1 1-1h3.5c.6 0 1 .4 1 1 0 1.2.2 2.4.6 3.6.1.3 0 .7-.2 1z"/></svg></span>123-456-7890</div>
<div class="contact-line" style="top:2212px;color:#fff;font-size:14px"><span class="ico"><svg width="14" height="12" viewBox="0 0 14 12"><rect x="0" y="1" width="14" height="10" fill="#fff"/><path d="M0 1 L7 7 L14 1" stroke="#0a6b35" stroke-width="1.5" fill="none"/></svg></span>info@vorelan.com</div>
<div class="footer-brand"><span class="brand-mark"></span><span class="brand-name">VORELAN</span></div>

<svg class="up-tab" width="40" height="14" viewBox="0 0 40 14"><path d="M0 14 L8 0 L32 0 L40 14Z" fill="#e8141b"/><path d="M15 10 L20 5 L25 10" stroke="#fff" stroke-width="2" fill="none"/></svg>
<div class="copyright">COPYRIGHT 2016 © VORELAN All Rights Reserved • Privacy Policy • Terms of Use</div>

</body>
</html>
```